Volbrey Inc Business Card

Looking to get an updated business card for a Contract Machining company (www.volbreyinc.example) - looking for a clean design the portrays the technical nature of the business - colors can follow the website design and be in any combination that makes sense (red black, white, metallic or silver) - logos attached for use also. Would like space for: Name, title, business phone (555 214-3086), cell phone , website (www.volbreyinc.example) - possibly QR code could be integrated for website (designer choice), business address - 418 Harlow Bend, Frankenmuth, MI 48199 (cards will be for 4 employees, I will either need to modify a template or I can provide individual information)
Target Market(s)
Aerospace, defense and medical device manufacturing companies that need machining
Industry/Entity Type
Machining for aerospace, defense, medical
Contact Information for Business Card
Name, Title, Business Phone, Cell Phone, email, business website and business address
Look and feel

```html
<!DOCTYPE html>
<html lang="en">
<head>
<meta charset="utf-8">
<title>Volbrey Inc Business Card</title>
<link href="https://fonts.googleapis.com/css2?family=Montserrat:wght@400;500;600&display=swap" rel="stylesheet">
<style>
  :root {
    --backdrop: #e6e1d9;
    --card-white: #ffffff;
    --brand-red: #b01c22;
    --emblem-red: #c0392b;
    --back-red: #ad1f26;
    --back-deep: #8e1419;
    --back-light: #c95a5c;
    --ink: #1d1d1d;
  }
  * { margin: 0; padding: 0; box-sizing: border-box; }
  html, body { width: 900px; height: 1200px; overflow: hidden; }
  body {
    background: var(--backdrop);
    font-family: "Montserrat", Arial, sans-serif;
    position: relative;
  }
  .card {
    position: absolute;
    border-radius: 22px;
    overflow: hidden;
    box-shadow: 0 6px 14px rgba(0,0,0,0.25);
  }
  .card-front {
    left: 80px; top: 131px; width: 742px; height: 440px;
    background: var(--card-white);
  }
  .brand-mark {
    position: absolute;
    left: 136px; top: 139px;
    width: 200px; height: 200px;
    border-radius: 50%;
    background: var(--emblem-red);
    display: flex; align-items: center; justify-content: center;
  }
  .brand-name {
    color: var(--card-white);
    font-weight: 600;
    font-size: 24px;
    text-align: center;
    line-height: 1.2;
  }
  .divider {
    position: absolute;
    left: 354px; top: 131px;
    width: 3px; height: 210px;
    background: var(--brand-red);
  }
  .contact {
    position: absolute;
    left: 373px; top: 127px;
    color: var(--ink);
  }
  .person-name {
    color: var(--brand-red);
    font-weight: 600;
    font-size: 27px;
    line-height: 32px;
  }
  .person-title { font-size: 16px; line-height: 20px; }
  .address { font-size: 16px; line-height: 20px; margin-top: 17px; }
  .lines { list-style: none; margin-top: 14px; }
  .lines li {
    display: flex; align-items: center;
    font-size: 16px; line-height: 23px;
  }
  .lines svg { width: 16px; height: 16px; margin-right: 8px; fill: var(--brand-red); }
  .card-back {
    left: 78px; top: 637px; width: 744px; height: 443px;
    background: var(--back-red);
  }
  .back-pattern {
    position: absolute; inset: 0;
    background: radial-gradient(ellipse at 0% 0%, var(--back-light) 0%, var(--back-red) 45%, var(--back-deep) 100%);
  }
  .back-seal {
    position: absolute;
    left: 555px; top: 266px;
    width: 84px; height: 84px;
    border-radius: 50%;
    background: var(--card-white);
    display: flex; align-items: center; justify-content: center;
    color: var(--brand-red);
    font-weight: 600; font-size: 12px; text-align: center; line-height: 1.2;
  }
</style>
</head>
<body>
  <section class="card card-front">
    <div class="brand-mark"><span class="brand-name">Volbrey<br>Inc</span></div>
    <div class="divider"></div>
    <div class="contact">
      <h1 class="person-name">Darlen Moore</h1>
      <p class="person-title">Owner</p>
      <p class="address">418 Harlow Bend,<br>Frankenmuth, MI 48199</p>
      <ul class="lines">
        <li><svg viewBox="0 0 24 24"><path d="M6.6 10.8a15 15 0 0 0 6.6 6.6l2.2-2.2a1 1 0 0 1 1-.25 11.4 11.4 0 0 0 3.6.6 1 1 0 0 1 1 1V20a1 1 0 0 1-1 1A17 17 0 0 1 3 4a1 1 0 0 1 1-1h3.5a1 1 0 0 1 1 1c0 1.25.2 2.45.6 3.6a1 1 0 0 1-.25 1z"/></svg>555 214-3086</li>
        <li><svg viewBox="0 0 24 24"><path d="M2 8c3-3 17-3 20 0v2h-5V8H7v2H2zM5 12h14l2 8H3zm7 2a2.5 2.5 0 1 0 0 5 2.5 2.5 0 0 0 0-5z"/></svg>555 214-3086</li>
        <li><svg viewBox="0 0 24 24"><path d="M2 5h20v14H2zm2 2v.5l8 5.5 8-5.5V7z"/></svg>info@volbreyinc.example</li>
        <li><svg viewBox="0 0 24 24"><path d="M12 2a10 10 0 1 0 0 20 10 10 0 0 0 0-20zm-1 17.9A8 8 0 0 1 4.2 10L9 15v1a2 2 0 0 0 2 2zm6.9-2.5A2 2 0 0 0 16 16h-1v-3a1 1 0 0 0-1-1H8v-2h2a1 1 0 0 0 1-1V7h2a2 2 0 0 0 2-2v-.4a8 8 0 0 1 2.9 12.8z"/></svg>www.volbreyinc.example</li>
      </ul>
    </div>
  </section>

  <section class="card card-back">
    <div class="back-pattern" role="img" aria-label="Repeating grid of embossed emblem circles in tones of red"></div>
    <div class="back-seal"><span>Volbrey<br>Inc</span></div>
  </section>
</body>
</html>
```